Boutique Health and Fitness Personal Training Studio

I would like to have a brochure designed which provides a detailed description of the services offered in my business.
I have personal training studio, We look after people from early 20's to 90's, healthy to very unhealthy.
We conduct:
A consultation
An assessment
A personalised program
Personalised training sessions
I would like to base the design around the colours of my logo (attached) and use some of (or all of) the images and information I have also attached.
I would be happy with your own images included also.

Target Market(s)

20 to 90 year olds

Industry/Entity Type

Business

Font styles to use
Serif
Sans Serif

Colors
9bcb3c
add136
cadf82
eaf2ce

Requirements
Must have
• Colour and images of fitness.
• 8.5x14 legal
• Tri fold
• 2 folds with 3 faces back n front
Nice to have
• The feeling of wellbeing
Should not have
• This is not a gym.
• It should have the feel of a private relaxed environment

```html
<!DOCTYPE html>
<html lang="en">
<head>
<meta charset="utf-8">
<title>Cedar Wellness Studio – Tri-fold Brochure</title>
<link href="https://fonts.googleapis.com/css2?family=Lato:wght@400;700&family=Roboto+Condensed:wght@400;700&display=swap" rel="stylesheet">
<style>
:root{
  --green:#5e8a22;
  --green-bright:#7fb22e;
  --green-light:#8fc23f;
  --charcoal:#2a2b29;
  --paper:#f4f4f2;
  --mist:#e6e7e4;
  --white:#ffffff;
  --ink:#1d1d1b;
  --stage:#ece9e4;
}
*{margin:0;padding:0;box-sizing:border-box}
html,body{width:907px;height:1200px;overflow:hidden;background:var(--stage)}
body{position:relative;font-family:"Lato",Arial,sans-serif;color:var(--white)}
.sheet{position:absolute;left:38px;width:830px;height:505px;box-shadow:0 4px 14px rgba(0,0,0,.25);overflow:hidden}
.sheet--outside{top:72px}
.sheet--inside{top:632px}
.panel{position:absolute;top:0;height:505px;overflow:hidden}
.panel--one{left:0;width:275px}
.panel--two{left:275px;width:277px}
.panel--three{left:552px;width:278px}
.shape{position:absolute;left:0;top:0;width:100%;height:100%}
.heading{font-family:"Roboto Condensed",Arial,sans-serif;font-weight:700;font-size:14px;line-height:1.25}
.body-copy{font-size:9.4px;line-height:1.32}
.text-block{position:absolute}
.brand{display:flex;align-items:center;gap:6px;font-family:"Lato",Arial,sans-serif;font-weight:700;font-size:15px;color:var(--green)}
.brand__dot{width:12px;height:12px;border-radius:50%;background:var(--green-bright)}

/* outside */
.cover-left{background:var(--green)}
.cover-left .heading{margin-top:10px}
.cover-left .fact{font-size:12.5px;margin-top:6px}
.parking{display:inline-block;margin-top:12px;padding:3px 5px;background:#3d4a2a;border-radius:3px;font-family:"Roboto Condensed",Arial,sans-serif;font-weight:700;font-size:14.5px;color:#b7d77a}
.cover-middle{background:linear-gradient(#fdfdfd 0%,var(--mist) 60%,#d9d9d7 100%)}
.contact{position:absolute;left:0;top:78px;width:100%;text-align:center;color:var(--ink)}
.contact .brand{justify-content:center;margin-bottom:18px}
.contact__unit{font-family:"Roboto Condensed",Arial,sans-serif;font-weight:700;font-size:14px;line-height:1.3}
.contact__line{font-size:10px;font-weight:700;margin-top:4px}
.contact__call{font-family:"Roboto Condensed",Arial,sans-serif;font-weight:700;font-size:13px;margin-top:4px}
.contact__visit{font-family:"Roboto Condensed",Arial,sans-serif;font-weight:700;font-size:14px;margin-top:6px}
.tagline{position:absolute;right:34px;top:358px;text-align:right;font-family:"Roboto Condensed",Arial,sans-serif;text-transform:uppercase}
.tagline__big{font-weight:700;font-size:24px;color:var(--green-light);letter-spacing:.3px}
.tagline__small{font-size:14px;line-height:1.3}
.tagline .brand{justify-content:flex-end;margin-top:22px;color:var(--white);font-size:17px}

/* inside */
.intro{background:var(--paper);color:var(--ink)}
.intro .heading{color:var(--green)}
.details{background:var(--green)}
.details .heading{margin-top:8px;margin-bottom:4px}
.details .body-copy{text-align:justify}
.footer-strip{position:absolute;left:0;bottom:0;width:275px;height:18px;background:var(--charcoal)}
</style>
</head>
<body>

<!-- Outside -->
<section class="sheet sheet--outside">
  <div class="panel panel--one cover-left">
    <div class="text-block" style="left:30px;top:36px;width:228px">
      <h2 class="heading">Your sessions</h2>
      <p class="body-copy" style="margin-top:6px">Training at the studio is professional and caring, but focused and challenging. Typically each session will take approximately 60 minutes. Training times can be organized to suit your needs with early mornings and evenings available.</p>
      <h2 class="heading" style="margin-top:14px">The Cost</h2>
      <p class="fact">$45 paid in blocks of 5 or 10 sessions</p>
      <h2 class="heading" style="margin-top:8px">Health fund claimable</h2>
      <p class="fact">Open 7 days</p>
      <span class="parking">Ample private parking available</span>
    </div>
    <svg class="shape" viewBox="0 0 275 505" aria-hidden="true">
      <path d="M0,280 Q170,262 275,372 L275,505 L0,505Z" fill="#ffffff"/>
    </svg>
    <svg class="shape" viewBox="0 0 275 505" role="img" aria-label="Photo: trainer guiding a client in a red shirt through a shoulder stretch">
      <defs><linearGradient id="stretchPhoto" x1="0" y1="0" x2="1" y2="1"><stop offset="0" stop-color="#b9b6b1"/><stop offset=".45" stop-color="#a9453c"/><stop offset="1" stop-color="#e4e2de"/></linearGradient></defs>
      <path d="M0,292 Q160,276 262,380 L262,505 L0,505Z" fill="url(#stretchPhoto)"/>
    </svg>
  </div>

  <div class="panel panel--two cover-middle">
    <svg class="shape" viewBox="0 0 277 505" role="img" aria-label="Photo: dumbbells, vegetables, a water bottle and a tape measure with a faint runner behind">
      <defs><linearGradient id="foodPhoto" x1="0" y1="0" x2="0" y2="1"><stop offset="0" stop-color="#e2e3e0" stop-opacity="0"/><stop offset=".45" stop-color="#9aa88a"/><stop offset=".75" stop-color="#b9a45a"/><stop offset="1" stop-color="#7a5a3c"/></linearGradient></defs>
      <rect x="0" y="270" width="277" height="235" fill="url(#foodPhoto)"/>
    </svg>
    <div class="contact">
      <div class="brand"><span class="brand__dot"></span>Cedar Wellness Studio</div>
      <p class="contact__unit">Unit 12<br>Level 2</p>
      <p class="contact__line">8 Willowmere Lane Fernhill</p>
      <p class="contact__call">call-0400 555 217</p>
      <p class="contact__visit">visit us</p>
      <p class="contact__line" style="margin-top:0">www.cedarwellnessstudio.com.au</p>
    </div>
  </div>

  <div class="panel panel--three" style="background:var(--paper)">
    <svg class="shape" viewBox="0 0 278 505" aria-hidden="true">
      <path d="M0,505 L0,430 Q40,290 278,272 L278,505Z" fill="var(--green-bright)"/>
      <path d="M12,505 L12,440 Q55,300 278,284 L278,505Z" fill="var(--charcoal)"/>
      <path d="M22,0 Q30,200 130,245 Q200,275 278,262 L278,0Z" fill="var(--green)"/>
    </svg>
    <svg class="shape" viewBox="0 0 278 505" role="img" aria-label="Photo: muscular man working out on a cable machine">
      <defs><linearGradient id="cablePhoto" x1="0" y1="0" x2="1" y2="1"><stop offset="0" stop-color="#6d7472"/><stop offset=".5" stop-color="#b07f63"/><stop offset="1" stop-color="#243338"/></linearGradient></defs>
      <path d="M32,0 Q40,190 135,232 Q200,258 278,248 L278,0Z" fill="url(#cablePhoto)"/>
    </svg>
    <div class="tagline">
      <p class="tagline__big">Over 25 years</p>
      <p class="tagline__small">of experience managing</p>
      <p class="tagline__small">personal health and fitness</p>
      <div class="brand"><span class="brand__dot"></span>Cedar Wellness Studio</div>
    </div>
  </div>
</section>

<!-- Inside -->
<section class="sheet sheet--inside">
  <div class="panel panel--one intro">
    <svg class="shape" viewBox="0 0 275 505" aria-hidden="true">
      <path d="M0,0 L275,0 L275,40 Q290,190 150,248 Q70,272 0,250Z" fill="var(--green)"/>
    </svg>
    <svg class="shape" viewBox="0 0 275 505" role="img" aria-label="Photo: woman exercising on a cross-trainer">
      <defs><linearGradient id="trainerPhoto" x1="0" y1="0" x2="1" y2="1"><stop offset="0" stop-color="#5c5f63"/><stop offset=".5" stop-color="#d2b49c"/><stop offset="1" stop-color="#e9eef0"/></linearGradient></defs>
      <path d="M0,0 L262,0 L262,40 Q276,180 145,234 Q70,258 0,238Z" fill="url(#trainerPhoto)"/>
    </svg>
    <div class="text-block" style="left:30px;top:280px;width:228px">
      <h2 class="heading">Personalised Care in<br>Fitness and Health</h2>
      <p class="body-copy" style="margin-top:3px">Exercise programs for all levels of health and fitness and all age groups.Experience in managing a wide range of chronic health conditions.</p>
      <h2 class="heading" style="margin-top:8px">Experienced professionals<br>caring for your wellbeing</h2>
      <p class="body-copy" style="margin-top:6px">Exercise Physiologist with over 25 years of experience managing the health and fitness needs of the community.</p>
      <div class="brand" style="margin-top:14px;margin-left:26px"><span class="brand__dot"></span>Cedar Wellness Studio</div>
    </div>
    <div class="footer-strip"></div>
  </div>

  <div class="panel panel--two details">
    <div class="text-block" style="left:27px;top:30px;width:230px">
      <h2 class="heading">What to Expect</h2>
      <p class="body-copy">On arrival at the studio you will be asked to complete a questionnaire, which will provide us with information regarding your background with health and fitness, as well as your goals and objectivesPlease bring any relevant medical information from medical practitioners or health professionals that you feel may impact on your program.</p>
      <h2 class="heading" style="margin-top:12px">Consultation</h2>
      <p class="body-copy">A consultation will allow you to share your thoughts, concerns and objectives, as well as provide you with ample opportunity to expand on the answers from your questionnaire relating to your prior and current health, medical and physical concerns.</p>
      <h2 class="heading" style="margin-top:10px">Nutrition</h2>
      <p class="body-copy">Nutrition is central to an effective program, as it will provide you with maximal energy for exercise as well as keeping yourself lean and healthy for a long term fitter lifestyle. Cedar Wellness Studio provides initial monitoring and ongoing modification in accordance with your needs.</p>
    </div>
    <svg class="shape" viewBox="0 0 277 505" role="img" aria-label="Photo: smiling woman seated cross-legged holding a dumbbell and a plate of vegetables">
      <defs><radialGradient id="balancePhoto" cx=".5" cy=".55" r=".55"><stop offset="0" stop-color="#e7a6c2"/><stop offset=".6" stop-color="#c9c2b6"/><stop offset="1" stop-color="#5e8a22" stop-opacity="0"/></radialGradient></defs>
      <ellipse cx="135" cy="420" rx="100" ry="85" fill="url(#balancePhoto)"/>
    </svg>
  </div>

  <div class="panel panel--three details">
    <div class="text-block" style="left:22px;top:30px;width:232px">
      <h2 class="heading">Assessment</h2>
      <p class="body-copy">An assessment will be conducted to provide us both with a baseline measure of your cardiovascular fitness, strength, flexibility, balance and body composition measures. These measures provide us with a reference for program design and also to indicate improvements along the way.</p>
      <h2 class="heading" style="margin-top:12px">The program</h2>
      <p class="body-copy">Your program will be designed with consideration to your health and fitness background, you objectives and your strengths and weaknesses. It will be personally tailored to your needs and provide you with a plan to focus your energies on.</p>
    </div>
    <svg class="shape" viewBox="0 0 278 505" aria-hidden="true">
      <path d="M0,505 Q10,340 150,300 Q230,282 278,290 L278,505Z" fill="var(--green-bright)"/>
    </svg>
    <svg class="shape" viewBox="0 0 278 505" role="img" aria-label="Photo: silhouettes of a woman and a trainer doing lunges against a white background">
      <defs><linearGradient id="lungePhoto" x1="0" y1="0" x2="0" y2="1"><stop offset="0" stop-color="#ffffff"/><stop offset=".55" stop-color="#eef0f2"/><stop offset="1" stop-color="#9aa3ac"/></linearGradient></defs>
      <path d="M16,505 Q26,352 155,314 Q230,296 278,302 L278,505Z" fill="url(#lungePhoto)"/>
    </svg>
  </div>
</section>

</body>
</html>
```